Website for 3d printing & other services

Hi, i'm after a website to sell my 3d printed automotive parts as well as sell my 3d printing services & other services.

There's a few things i need the website to have:

- Automatic 3d print quoting based on the file the client uploads to the website.
- Shop function where i can sell my custom automotive parts
- 3D printing technologies offered are SLA & FDM
- My business can offer 3d printing, 3d scanning, 3d cad design, cnc machining, steel fabrication, drafting services.

The color design is to suit my logo which is Black, orange & white.

Target Market(s)

3d printing, automotive, fabrication

Industry/Entity Type

General manufacturing & Custom automotive parts

Coding

Coded - Design and coding required

Number of Pages Required

5+ page

Requirements
Must have
• Automatic 3d print quoting. Shop for my printed parts.

```html
<!DOCTYPE html>
<html lang="en">
<head>
<meta charset="utf-8">
<title>Kestrel Draft &amp; Design</title>
<link rel="stylesheet" href="https://fonts.googleapis.com/css2?family=Josefin+Sans:wght@600;700&family=Lato:wght@400;700&display=swap">
<style>
:root{
  --orange:#f57c00;
  --black:#111111;
  --ink:#222222;
  --muted:#555555;
  --grey-bg:#f4f4f4;
  --card:#f3f3f3;
  --field:#f1f1f1;
  --white:#ffffff;
  --wood:#a8592c;
  --wood-dark:#6b3419;
  --plate:#5c5d60;
  --burgundy:#7a2a33;
  --fleece:#e9e1d8;
}
*{box-sizing:border-box;margin:0;padding:0}
html,body{width:1200px;height:3951px;overflow:hidden}
body{position:relative;background:var(--white);font-family:"Lato",sans-serif;color:var(--ink)}
.abs{position:absolute}
.display{font-family:"Josefin Sans",sans-serif;font-weight:700;letter-spacing:2px;color:var(--black);text-transform:uppercase}
.btn{position:absolute;display:flex;align-items:center;justify-content:center;gap:8px;background:var(--orange);color:var(--white);font-family:"Josefin Sans",sans-serif;font-weight:700;text-transform:uppercase;letter-spacing:1px;border-radius:22px;white-space:nowrap}
/* header */
.hero-photo{left:0;top:0;width:1200px;height:835px;
  background:
    radial-gradient(ellipse 120px 110px at 90px 580px,#c9c5bd 0%,#7d7a74 55%,rgba(125,122,116,0) 100%),
    radial-gradient(ellipse 130px 110px at 1120px 520px,#cfcbc2 0%,#85817a 55%,rgba(133,129,122,0) 100%),
    radial-gradient(ellipse 160px 90px at 740px 420px,#b9b39f 0%,#6e6a5c 60%,rgba(110,106,92,0) 100%),
    radial-gradient(ellipse 700px 260px at 600px 560px,var(--burgundy) 0%,#8e4048 50%,rgba(142,64,72,0) 100%),
    linear-gradient(180deg,var(--fleece) 0%,#d9cfc4 45%,#b89a90 70%,#cfc3b8 100%)}
.hero-veil{left:0;top:0;width:1200px;height:835px;background:linear-gradient(180deg,rgba(255,255,255,.96) 0%,rgba(255,255,255,.75) 22%,rgba(255,255,255,.35) 45%,rgba(255,255,255,.1) 100%)}
.brand{font-family:"Josefin Sans",sans-serif;font-weight:700;color:var(--orange);text-transform:uppercase;white-space:nowrap;letter-spacing:.5px}
.brand .big{display:block}
.brand .small{display:block;color:var(--ink)}
.header-brand{left:107px;top:62px}
.header-brand .big{font-size:34px;line-height:36px}
.header-brand .small{font-size:15px;line-height:20px}
.nav{top:56px;font-size:15px;color:var(--ink)}
.login{left:959px;top:43px;width:129px;height:44px;border-radius:0 18px 0 18px;font-size:18px}
.hero-title{left:0;width:1200px;top:152px;text-align:center;font-size:64px;line-height:76px;letter-spacing:4px}
.get-started{left:511px;top:333px;width:178px;height:51px;border-radius:0 18px 0 18px;font-size:18px}
.hero-shot{left:160px;top:450px;width:903px;height:532px;
  background:
    radial-gradient(ellipse 340px 170px at 520px 270px,#7a7b7e 0%,var(--plate) 55%,rgba(92,93,96,0) 100%),
    radial-gradient(ellipse 260px 120px at 300px 150px,#6d6e71 0%,rgba(109,110,113,0) 100%),
    linear-gradient(160deg,#c9763f 0%,var(--wood) 35%,#8c4521 65%,var(--wood-dark) 100%)}
/* shop */
.section-title{left:0;width:1200px;text-align:center;font-size:38px}
.product{width:229px;height:338px;top:1149px;background:var(--card);border-radius:22px}
.product .thumb{position:absolute;left:35px;top:33px;width:159px;height:153px}
.product .name{position:absolute;top:216px;width:100%;text-align:center;font-family:"Josefin Sans",sans-serif;font-weight:700;font-size:18px;letter-spacing:1px;text-transform:uppercase}
.product .price{position:absolute;top:245px;width:100%;text-align:center;color:var(--orange);font-size:14px;font-weight:700;letter-spacing:1px}
.product .btn{left:40px;top:274px;width:149px;height:40px;font-size:11px}
/* services */
.services-band{left:0;top:1585px;width:1200px;height:666px;background:var(--grey-bg)}
.service{top:1762px;height:398px;border-radius:14px;overflow:hidden}
.service .label{position:absolute;left:23px;bottom:33px;font-family:"Josefin Sans",sans-serif;font-weight:700;font-size:26px;letter-spacing:2px;color:var(--white);text-transform:uppercase}
.service.active{background:radial-gradient(ellipse 200px 120px at 150px 90px,#ff9a3c 0%,var(--orange) 70%);height:403px}
.service.active p{position:absolute;left:28px;top:190px;width:260px;font-size:14px;line-height:26px;color:var(--white)}
.service.active .learn{position:absolute;left:28px;top:338px;font-family:"Josefin Sans",sans-serif;font-weight:700;font-size:17px;letter-spacing:1px;color:var(--white);text-decoration:underline;text-transform:uppercase}
.arrow{width:32px;height:32px;border-radius:50%;display:flex;align-items:center;justify-content:center}
/* tech */
.tech-img{border-radius:4px}
.tech-title{left:628px;top:2384px;font-size:42px;line-height:47px}
.tech-item{left:628px;font-family:"Josefin Sans",sans-serif;font-weight:700;font-size:26px;letter-spacing:1px;display:flex;align-items:center;gap:8px}
.tech-item i{width:13px;height:13px;border:3px solid var(--orange);border-radius:50%}
.tech-body{left:648px;top:2589px;width:450px;font-size:14px;line-height:30px;color:var(--muted)}
.link-small{font-family:"Josefin Sans",sans-serif;font-weight:700;font-size:13px;letter-spacing:1px;color:var(--ink);text-decoration:underline;text-transform:uppercase}
/* contact */
.footer{left:0;top:3371px;width:1200px;height:580px;background:var(--black)}
.contact{left:98px;top:2992px;width:1002px;height:545px;background:var(--white);border-radius:14px;box-shadow:0 0 18px rgba(0,0,0,.06)}
.field{background:var(--field);border-radius:24px;font-size:14px;color:#777;padding:15px 25px;display:flex;justify-content:space-between}
.footer-text{font-size:13px;line-height:20px;color:var(--white)}
.footer-brand{left:138px;top:3668px}
.footer-brand .big{font-size:46px;line-height:50px}
.footer-brand .small{font-size:22px;line-height:28px;color:var(--white)}
.ficon{width:36px;height:36px;border-radius:50%;background:var(--orange);display:flex;align-items:center;justify-content:center}
.social{width:28px;height:28px;border-radius:50%;border:1.5px solid var(--white);display:flex;align-items:center;justify-content:center}
.social span{width:8px;height:8px;border-radius:50%;background:var(--white)}
</style>
</head>
<body>

<header>
  <div class="abs hero-photo" role="img" aria-label="Photo of classic car dashboard gauges over a sheepskin cover"></div>
  <div class="abs hero-veil"></div>
  <div class="abs brand header-brand"><span class="big">Kestrel</span><span class="small">Draft &amp; Design</span></div>
  <nav>
    <span class="abs nav" style="left:390px">Home</span>
    <span class="abs nav" style="left:471px">Services We offer</span>
    <span class="abs nav" style="left:631px">Our Products</span>
    <span class="abs nav" style="left:763px">About Us</span>
    <span class="abs nav" style="left:865px">Contact</span>
  </nav>
  <a class="btn login">
    <svg width="13" height="14" viewBox="0 0 13 14"><circle cx="6.5" cy="4" r="3.5" fill="#fff"/><path d="M0 14c0-4 3-6 6.5-6S13 10 13 14z" fill="#fff"/></svg>Login</a>
  <h1 class="abs display hero-title">Welcome to<br>Kestrel Draft &amp; Design</h1>
  <a class="btn get-started">Get Started</a>
  <div class="abs hero-shot" role="img" aria-label="Photo of a 3D printed grey dashboard gauge panel on a wooden table"></div>
</header>

<section>
  <h2 class="abs display section-title" style="top:1068px">Automatic 3D Print</h2>
  <div class="abs product" style="left:97px"><div class="thumb" role="img" aria-label="Compact 3D printer" style="background:radial-gradient(ellipse 55px 70px at 80px 80px,#3a3b3e 0%,#8d8f93 45%,rgba(243,243,243,0) 100%)"></div><div class="name">Lorem Ipsum</div><div class="price">£620.00</div><a class="btn"><svg width="14" height="12" viewBox="0 0 14 12"><path d="M0 1h3l2 7h7l2-5H4" fill="none" stroke="#fff" stroke-width="2"/><circle cx="6" cy="11" r="1" fill="#fff"/><circle cx="11" cy="11" r="1" fill="#fff"/></svg>Add to cart</a></div>
  <div class="abs product" style="left:356px"><div class="thumb" role="img" aria-label="Open frame 3D printer" style="background:radial-gradient(ellipse 70px 70px at 80px 80px,#c9c2b6 0%,#9a8f80 40%,#e07a2a 55%,rgba(243,243,243,0) 100%)"></div><div class="name">Lorem Ipsum</div><div class="price">£620.00</div><a class="btn"><svg width="14" height="12" viewBox="0 0 14 12"><path d="M0 1h3l2 7h7l2-5H4" fill="none" stroke="#fff" stroke-width="2"/><circle cx="6" cy="11" r="1" fill="#fff"/><circle cx="11" cy="11" r="1" fill="#fff"/></svg>Add to cart</a></div>
  <div class="abs product" style="left:617px"><div class="thumb" role="img" aria-label="Enclosed black 3D printer" style="background:radial-gradient(ellipse 80px 65px at 80px 80px,#c0262e 0%,#2a2a2c 35%,#111 70%,rgba(243,243,243,0) 100%)"></div><div class="name">Lorem Ipsum</div><div class="price">£620.00</div><a class="btn"><svg width="14" height="12" viewBox="0 0 14 12"><path d="M0 1h3l2 7h7l2-5H4" fill="none" stroke="#fff" stroke-width="2"/><circle cx="6" cy="11" r="1" fill="#fff"/><circle cx="11" cy="11" r="1" fill="#fff"/></svg>Add to cart</a></div>
  <div class="abs product" style="left:876px"><div class="thumb" role="img" aria-label="3D scanner with monitor" style="background:radial-gradient(ellipse 80px 60px at 80px 80px,#dcdcdc 0%,#6f7378 40%,#2a3f57 60%,rgba(243,243,243,0) 100%)"></div><div class="name">Lorem Ipsum</div><div class="price">£620.00</div><a class="btn"><svg width="14" height="12" viewBox="0 0 14 12"><path d="M0 1h3l2 7h7l2-5H4" fill="none" stroke="#fff" stroke-width="2"/><circle cx="6" cy="11" r="1" fill="#fff"/><circle cx="11" cy="11" r="1" fill="#fff"/></svg>Add to cart</a></div>
</section>

<section>
  <div class="abs services-band"></div>
  <h2 class="abs display section-title" style="top:1666px">Services We Offer</h2>
  <div class="abs arrow" style="left:36px;top:1942px;background:var(--orange)"><svg width="10" height="10" viewBox="0 0 10 10"><path d="M6 1L2 5l4 4" fill="none" stroke="#fff" stroke-width="1.8"/></svg></div>
  <div class="abs arrow" style="left:1126px;top:1942px;background:#d6d6d6"><svg width="10" height="10" viewBox="0 0 10 10"><path d="M4 1l4 4-4 4" fill="none" stroke="#fff" stroke-width="1.8"/></svg></div>
  <div class="abs service" style="left:110px;width:306px;background:radial-gradient(ellipse 90px 110px at 230px 150px,#9c9c9c 0%,rgba(90,90,90,0) 100%),radial-gradient(ellipse 70px 90px at 70px 120px,#c7d0d8 0%,rgba(120,130,140,0) 100%),linear-gradient(180deg,#4a4a4a 0%,#222 60%,#101010 100%)" role="img" aria-label="Photo of a 3D printer printing a lattice part"><div class="label">3D Printing</div></div>
  <div class="abs service active" style="left:446px;width:304px">
    <svg class="abs" style="left:26px;top:54px" width="50" height="50" viewBox="0 0 50 50"><circle cx="25" cy="25" r="25" fill="#fff"/><rect x="15" y="16" width="20" height="17" rx="2" fill="none" stroke="#333" stroke-width="2"/><path d="M18 29l5-6 4 4 3-3 3 5" fill="none" stroke="#333" stroke-width="1.6"/></svg>
    <div class="label" style="top:150px;bottom:auto;left:28px">3D Scanning</div>
    <p>Lorem ipsum dolor sit amet, consectetur adipiscing elit, sed do eiusmod tempor incididunt ut labore et dolore magna aliqua. Quis ipsum suspendisse ultrices gravida.</p>
    <a class="learn">Learn More</a>
  </div>
  <div class="abs service" style="left:783px;width:305px;background:radial-gradient(ellipse 60px 120px at 250px 180px,#3a3f3a 0%,rgba(40,40,40,0) 100%),radial-gradient(ellipse 50px 60px at 90px 60px,#b9c3cc 0%,rgba(120,130,140,0) 100%),linear-gradient(180deg,#8c9aa8 0%,#2a2a2c 25%,#151515 100%)" role="img" aria-label="Photo of a black CAD designed dashboard panel with gauges"><div class="label">3D CAD Design</div></div>
</section>

<section>
  <div class="abs tech-img" style="left:112px;top:2349px;width:229px;height:444px;background:radial-gradient(ellipse 110px 220px at 120px 240px,#d9d5cc 0%,#a49f94 40%,rgba(60,58,54,0) 100%),linear-gradient(160deg,#2e2d2a,#4a4743 60%,#2a2926)" role="img" aria-label="Photo of a machined aluminium intake part"></div>
  <div class="abs tech-img" style="left:354px;top:2432px;width:229px;height:444px;background:radial-gradient(ellipse 55px 170px at 60px 230px,#1f2026 0%,#3b3e48 60%,rgba(210,196,180,0) 100%),radial-gradient(ellipse 45px 150px at 185px 200px,#1f2026 0%,#3b3e48 60%,rgba(210,196,180,0) 100%),linear-gradient(180deg,#dcd0c2,#cbb9a5)" role="img" aria-label="Photo of two black anodised brackets"></div>
  <h2 class="abs display tech-title">3D Printing<br>Technologies<br>Offered</h2>
  <div class="abs tech-item" style="top:2552px"><i></i>SLA</div>
  <p class="abs tech-body">Lorem ipsum dolor sit amet, consectetur adipiscing elit, sed do eiusmod tempor incididunt ut labore et dolore magna aliqua. Quis ipsum suspendisse ultrices gravida. Risus commodo viverra maecenas accumsan lacus vel facilisis.</p>
  <a class="abs link-small" style="left:648px;top:2724px">Learn More</a>
  <div class="abs" style="left:628px;top:2774px;width:452px;height:1px;background:#cfcfcf"></div>
  <div class="abs tech-item" style="top:2797px"><i></i>FDM</div>
</section>

<div class="abs footer"></div>

<section class="abs contact">
  <h2 class="abs display section-title" style="top:52px;width:1002px;font-size:42px">Contact Us</h2>
  <p class="abs" style="left:120px;top:113px;width:762px;text-align:center;font-size:15px;line-height:23px;color:var(--muted)">Lorem ipsum dolor sit amet, consectetur adipiscing elit, sed do eiusmod tempor incididunt ut labore et dolore magna aliqua. Quis ipsum suspendisse ultrices gravida.ilisis.</p>
  <div class="abs field" style="left:37px;top:204px;width:451px;height:49px">Name<svg width="12" height="13" viewBox="0 0 12 13"><circle cx="6" cy="3.5" r="3" fill="#555"/><path d="M0 13c0-4 3-6 6-6s6 2 6 6z" fill="#555"/></svg></div>
  <div class="abs field" style="left:502px;top:204px;width:459px;height:49px">Email<svg width="13" height="10" viewBox="0 0 13 10"><rect width="13" height="10" fill="#555"/><path d="M0 0l6.5 5L13 0" fill="none" stroke="#f1f1f1" stroke-width="1.2"/></svg></div>
  <div class="abs field" style="left:37px;top:278px;width:928px;height:134px;border-radius:26px">Message</div>
  <a class="btn" style="left:407px;top:444px;width:189px;height:52px;border-radius:0 18px 0 18px;font-size:16px">Send Message</a>
</section>

<footer>
  <div class="abs brand footer-brand"><span class="big">Kestrel</span><span class="small">Draft &amp; Design</span></div>
  <div class="abs ficon" style="left:453px;top:3676px"><svg width="12" height="16" viewBox="0 0 12 16"><path d="M6 0a6 6 0 0 0-6 6c0 4.5 6 10 6 10s6-5.5 6-10a6 6 0 0 0-6-6z" fill="#fff"/><circle cx="6" cy="6" r="2.2" fill="#f57c00"/></svg></div>
  <p class="abs footer-text" style="left:506px;top:3674px;width:220px">199 b Kestrel Draft &amp; design Lorem ipsum dolor sit amet,</p>
  <div class="abs ficon" style="left:453px;top:3734px"><svg width="14" height="10" viewBox="0 0 14 10"><rect width="14" height="10" rx="1" fill="#fff"/><path d="M0 0l7 5 7-5" fill="none" stroke="#f57c00" stroke-width="1.3"/></svg></div>
  <p class="abs footer-text" style="left:500px;top:3743px">Email<br>info@kestreldraft.com</p>
  <div class="abs ficon" style="left:743px;top:3677px"><svg width="15" height="15" viewBox="0 0 15 15"><path d="M3 0l3 3-2 2c1 2 4 5 6 6l2-2 3 3-2 3C6 15 0 9 0 3z" fill="#fff"/></svg></div>
  <p class="abs footer-text" style="left:801px;top:3686px">Phone<br>+1 888 888 8888</p>
  <div class="abs social" style="left:992px;top:3678px;background:var(--orange);border-color:var(--orange)"><span></span></div>
  <div class="abs social" style="left:1031px;top:3678px"><span></span></div>
  <div class="abs social" style="left:992px;top:3716px"><span></span></div>
  <div class="abs social" style="left:1031px;top:3716px"><span></span></div>
  <div class="abs" style="left:110px;top:3841px;width:979px;height:1px;background:#444"></div>
  <p class="abs footer-text" style="left:0;width:1200px;top:3883px;text-align:center;font-size:14px">©Copyrights 2023 Kestrel Draft &amp; design &nbsp;| &nbsp;&nbsp;All Rights Reserved</p>
</footer>

</body>
</html>
```